"Vine Hollow Excursions" is a top notch Santa Barbara County Wine Tour company.

We provide scenic, boutique and custom wine tours. I need the card to be clean and classy. I will provide our logo. I would like the logo to cover the back side of the card as an option and would like to see a couple color options other then our signature green and gold. I would like to see some creative options and let the designers come up with options.
I need cards for myself and my team. The final design should communicate "An authentic and boutique wine tour experience"
Please use my website for reference www.vinehollowexcursions.example

Target Market(s)

We have a wide range of clients from millennials to baby boomers

Industry/Entity Type

Tour

Contact Information for Business Card

Contact info:
Dale Morton
805-219-6384
info@vinehollowexcursions.example
vinehollowexcursions.example

Colors

Designer to choose colors to be used in the design.

Requirements
Must have
• my logo
Nice to have
• *I would like to have the backside side with the logo and the company statement
• "An authentic and boutique wine tour experience" as an option.
• *I would also like to see what the designers can create!
• *I would like to see an option that incorporates or social: instagram, yelp, trip advisor
Should not have
• I do not want it too busy.

```html
<!DOCTYPE html>
<html lang="en">
<head>
<meta charset="utf-8">
<title>Vine Hollow Excursions — Business Card</title>
<link href="https://fonts.googleapis.com/css2?family=Marcellus&family=PT+Sans:wght@400;700&display=swap" rel="stylesheet">
<style>
  :root {
    --backdrop: #2b2b2b;
    --paper: #f1f1f0;
    --vine-green: #2a6440;
    --vine-green-light: #6f9a7c;
    --on-green: #ffffff;
    --gold: #9a7a58;
    --icon-a: #b89a78;
    --icon-b: #5f9a3e;
    --icon-c: #d8322e;
  }
  * { margin: 0; padding: 0; box-sizing: border-box; }
  html, body { width: 1200px; height: 960px; overflow: hidden; }
  body { background: var(--backdrop); position: relative; font-family: "PT Sans", sans-serif; }

  .card {
    position: absolute;
    width: 600px;
    height: 343px;
    background: var(--paper);
    overflow: hidden;
  }
  .card--front { left: 314px; top: 113px; }
  .card--back  { left: 311px; top: 472px; }

  .front__scene {
    position: absolute;
    left: 0; top: 0;
    width: 600px; height: 222px;
    background: linear-gradient(170deg, var(--paper) 0%, var(--paper) 45%, var(--vine-green-light) 78%, var(--vine-green) 100%);
  }
  .front__band {
    position: absolute;
    left: 0; top: 222px;
    width: 600px; height: 121px;
    background: var(--vine-green);
    color: var(--on-green);
    text-align: center;
  }
  .front__name {
    position: absolute;
    left: 0; right: 0; top: 0;
    font-family: "Marcellus", serif;
    font-size: 25px;
    letter-spacing: 0.5px;
    line-height: 30px;
    padding-left: 2px;
  }
  .front__contact {
    position: absolute;
    left: 0; right: 0; top: 33px;
    font-size: 15px;
    line-height: 20px;
    padding-left: 2px;
  }
  .front__tagline {
    position: absolute;
    left: 0; right: 0; top: 54px;
    font-size: 15.5px;
    font-weight: 700;
    line-height: 20px;
  }
  .front__social {
    position: absolute;
    left: 0; top: 80px;
    width: 600px; height: 24px;
  }

  .back__brand {
    position: absolute;
    left: 0; right: 0; top: 200px;
    display: flex;
    align-items: center;
    justify-content: center;
    gap: 12px;
  }
  .back__mark {
    width: 18px; height: 18px;
    background: var(--vine-green);
  }
  .back__name {
    font-family: "Marcellus", serif;
    font-size: 30px;
    letter-spacing: 1px;
    color: var(--gold);
  }
</style>
</head>
<body>
  <section class="card card--front" aria-label="Card front">
    <div class="front__scene" role="img" aria-label="Illustration of a rising sun with rays over rolling green mountains"></div>
    <div class="front__band">
      <p class="front__name">DALE MORTON</p>
      <p class="front__contact">805-219-6384 |info@vinehollowexcursions.example |vinehollowexcursions.example</p>
      <p class="front__tagline">An authentic &amp; boutique wine tour experience</p>
      <svg class="front__social" viewBox="0 0 600 24" aria-label="Social profiles">
        <defs>
          <linearGradient id="rule-left" x1="0" x2="1">
            <stop offset="0" stop-color="#ffffff" stop-opacity="0"/>
            <stop offset="1" stop-color="#ffffff" stop-opacity="0.9"/>
          </linearGradient>
          <linearGradient id="rule-right" x1="0" x2="1">
            <stop offset="0" stop-color="#ffffff" stop-opacity="0.9"/>
            <stop offset="1" stop-color="#ffffff" stop-opacity="0"/>
          </linearGradient>
        </defs>
        <rect x="95" y="11" width="152" height="1.5" fill="url(#rule-left)"/>
        <rect x="353" y="11" width="152" height="1.5" fill="url(#rule-right)"/>
        <rect x="258" y="2" width="21" height="21" rx="4" fill="var(--icon-a)"/>
        <rect x="289" y="2" width="21" height="21" rx="4" fill="var(--icon-b)"/>
        <rect x="320" y="2" width="21" height="21" rx="4" fill="var(--icon-c)"/>
      </svg>
    </div>
  </section>

  <section class="card card--back" aria-label="Card back">
    <div class="back__brand">
      <span class="back__mark"></span>
      <span class="back__name">Vine Hollow Excursions</span>
    </div>
  </section>
</body>
</html>
```